Polished Comb salon has created a lotion and needs help titling.Tides by polished comb ?Polis

The product is for a lotion bottle , my prototype lotion bottle size is an 8oz black lotion bottle with pump. I want the label in florescent green. It should tap into the emotion of potential buyers. The design should say choose me 😀(not literally ). Though the text should be clear and punchy . I.e " the skin multi-vitamin." I'm looking for a designer intrigued by the thought of my lotion. The label should be georgeous,informative, with visuals that immediately convey what my product is and how it works.Not distracting, but clear and punchy, with no expectation of someone to read more than a couple of words.The text should support the visual in a way the visual could not. It seems that nowadays visuals are taking over with very little text. The font,color , or punch of color should be enticing.
So here are some particular ideas of points about the lotion that could possibly be put on back as is done by lotion makers.
.ingredients
.TSA approved
.portion of proceeds go to lunch for little ones
.TC circled ( which is for pending trademark)
. I would like the word New in fluorescent on the bottle
.P.O Box address of place of manufacturing product.
. To help skin stay slightly moist,soft,and flexible with a smooth fine grained texture.

Target Market(s)

its a lotion so I want it available for all

Industry/Entity Type

Barber

Colors
9bcb3c

Requirements
Must have
• the word" Tides" and By polished comb...the word new on the bottle visible

```html
<!DOCTYPE html>
<html lang="en">
<head>
<meta charset="utf-8">
<title>Tides by Polished Comb – Lotion Label</title>
<link href="https://fonts.googleapis.com/css2?family=Montserrat:wght@400;600;700;800&display=swap" rel="stylesheet">
<style>
  :root {
    --backdrop: #e4e4e4;
    --label-black: #1b1b1b;
    --fluoro-green: #9bcb3c;
    --badge-green: #b6e04a;
    --ink: #1b1b1b;
    --white: #ffffff;
  }
  * { box-sizing: border-box; margin: 0; padding: 0; }
  html, body {
    width: 1200px;
    height: 1200px;
    overflow: hidden;
    background: var(--backdrop);
    font-family: "Montserrat", sans-serif;
  }
  .canvas {
    position: relative;
    width: 1200px;
    height: 1200px;
  }
  .label {
    position: absolute;
    left: 150px;
    top: 150px;
    width: 900px;
    height: 900px;
    background: var(--label-black);
    overflow: hidden;
  }
  .label__panel {
    position: absolute;
    left: 0;
    top: 0;
    width: 900px;
    height: 520px;
  }
  .badge-new {
    position: absolute;
    left: 70px;
    top: 60px;
    width: 140px;
    height: 140px;
    border-radius: 50%;
    background: var(--badge-green);
    display: flex;
    align-items: center;
    justify-content: center;
    color: var(--white);
    font-weight: 800;
    font-size: 36px;
    letter-spacing: 1px;
    transform: rotate(-14deg);
  }
  .brand {
    position: absolute;
    left: 0;
    width: 900px;
    top: 150px;
    text-align: center;
  }
  .brand__name {
    display: inline-flex;
    align-items: center;
    gap: 22px;
    font-weight: 400;
    font-size: 190px;
    line-height: 1;
    letter-spacing: -6px;
    color: var(--ink);
  }
  .brand__dot {
    width: 54px;
    height: 54px;
    border-radius: 50%;
    background: var(--ink);
  }
  .brand__by {
    margin-top: 6px;
    font-weight: 800;
    font-size: 30px;
    letter-spacing: 0.5px;
    color: var(--ink);
    text-transform: uppercase;
  }
  .tagline-pill {
    position: absolute;
    left: 50%;
    top: 455px;
    transform: translateX(-50%);
    padding: 14px 34px;
    border: 4px solid var(--white);
    border-radius: 14px;
    background: var(--label-black);
    color: var(--fluoro-green);
    font-weight: 700;
    font-size: 31px;
    white-space: nowrap;
    text-transform: uppercase;
  }
  .benefit {
    position: absolute;
    left: 0;
    width: 900px;
    top: 575px;
    text-align: center;
    color: var(--fluoro-green);
  }
  .benefit__headline {
    font-weight: 700;
    font-size: 38px;
    line-height: 1.4;
    text-transform: uppercase;
  }
  .benefit__body {
    margin: 16px auto 0;
    width: 620px;
    font-weight: 600;
    font-size: 20px;
    line-height: 1.55;
  }
  .net-weight {
    position: absolute;
    left: 0;
    width: 900px;
    top: 800px;
    text-align: center;
    color: var(--fluoro-green);
    font-weight: 600;
    font-size: 30px;
    line-height: 1.2;
  }
</style>
</head>
<body>
  <main class="canvas">
    <section class="label" aria-label="Tides lotion bottle label">
      <svg class="label__panel" viewBox="0 0 900 520" aria-hidden="true">
        <path d="M0 0 H900 V390 Q900 480 810 480 H90 Q0 480 0 390 Z" fill="var(--fluoro-green)"/>
      </svg>

      <div class="badge-new">NEW</div>

      <div class="brand">
        <div class="brand__name"><span>Tides</span><span class="brand__dot"></span></div>
        <div class="brand__by">By Polished Comb</div>
      </div>

      <div class="tagline-pill">The Skin Multi-Vitamin Lotion</div>

      <div class="benefit">
        <p class="benefit__headline">Keeps skin soft,<br>smooth and slightly moist</p>
        <p class="benefit__body">Lorem ipsum dolor sit amet, consectetur adipisicing elit, sed do eiusmod tempor.</p>
      </div>

      <p class="net-weight">Net Weight: 8oz</p>
    </section>
  </main>
</body>
</html>
```